High-end construction company needs a business card design

We need a modern looking business card that draws people in, is memorable and looks so good people will want to sick it on their fridges.
On the first side what is needed are:
Logo
My name - Tomasz Brelwik
Title - Managing Director
Website - www.varkelt.co.uk
Email - tomasz@varkelt.co.uk
Telephone - 020 5194 6281
Mobile - 07845139072
On the back side was is needed is a list of all the services we provide:
-Kitchen Renovations
-Bathroom Renovations
-House Renovations
-Garage Conversions
-Extensions
-Loft Conversions
-Conservatories
-Carpentry
-Tiling
-Electrical
-Plumbing & Heating
-Bricklaying
-Landscaping
-Decorating
-Plastering
We would like the colours to be the same shades as on the logo with grey or black for the words.
Target Market(s)
Anyone who needs building work done
Contact Information for Business Card
This business card is for a construction company which strives to deliver excellent service and quality.
The look and feel of the card should represent this.
Requirements
Must have
- On the first side what is needed are:
Logo
My name - Tomasz Brelwik
Title - Managing Director
Website - www.varkelt.co.uk
Email - tomasz@varkelt.co.uk
Telephone - 020 5194 6281
Mobile - 07845139072
Nice to have
- Cool looking features

```html
<!DOCTYPE html>
<html lang="en">
<head>
<meta charset="utf-8">
<title>Varkelt Construction Ltd – Business Card</title>
<link rel="stylesheet" href="https://fonts.googleapis.com/css2?family=Arimo:wght@400;700&display=swap">
<style>
  :root {
    --backdrop: #2a2624;
    --card: #0b0b0b;
    --green: #76c043;
    --green-dark: #4f9a2e;
    --text: #f2f2f2;
    --grey: #a6a6a6;
    --rule: #4a4a4a;
  }
  * { margin: 0; padding: 0; box-sizing: border-box; }
  html, body { width: 1200px; height: 842px; overflow: hidden; }
  body {
    background: var(--backdrop);
    font-family: "Arimo", Arial, sans-serif;
    display: flex;
    align-items: center;
    justify-content: center;
    gap: 40px;
  }
  .card {
    position: relative;
    width: 540px;
    height: 309px;
    background: var(--card);
    overflow: hidden;
    box-shadow: 0 14px 30px rgba(0,0,0,.55);
  }
  /* contact side */
  .band { position: absolute; left: 0; right: 0; height: 9px; background: var(--green); }
  .band--top { top: 12px; }
  .band--bottom { bottom: 12px; }
  .identity { position: absolute; top: 46px; left: 0; right: 0; text-align: center; }
  .identity__name {
    color: var(--green); font-weight: 700; font-size: 19px;
    letter-spacing: .5px; text-transform: uppercase;
  }
  .identity__title { color: var(--grey); font-size: 13px; margin-top: 2px; }
  .rule { width: 150px; height: 1px; background: var(--rule); margin: 12px auto; }
  .contact { color: var(--grey); font-size: 13px; line-height: 1.55; }
  .contact b { color: var(--green); font-weight: 700; }
  .contact .web { color: var(--green); }
  .services {
    position: absolute; left: 42px; right: 30px; top: 190px;
    display: flex; gap: 26px;
  }
  .services ul { list-style: none; }
  .services li {
    color: var(--text); font-size: 12.5px; line-height: 1.3;
    display: flex; align-items: center; gap: 7px; white-space: nowrap;
  }
  .services li::before {
    content: ""; width: 6px; height: 6px; border-radius: 50%;
    background: var(--green); flex: none;
  }
  /* brand side */
  .tab { position: absolute; width: 34px; height: 40px; background: var(--green); }
  .tab::after {
    content: ""; position: absolute; top: 0; right: -5px; width: 5px; height: 100%;
    background: var(--green-dark);
  }
  .tab--left { left: 0; top: 150px; }
  .tab--right { right: 32px; top: 38px; }
  .brand {
    position: absolute; inset: 0;
    display: flex; flex-direction: column; align-items: center; justify-content: center;
    color: var(--green); font-weight: 700; text-transform: uppercase;
  }
  .brand__name { font-size: 54px; letter-spacing: 2px; line-height: 1; }
  .brand__sub { font-size: 14px; letter-spacing: 3px; margin-top: 8px; }
</style>
</head>
<body>
  <section class="card card--contact">
    <div class="band band--top"></div>
    <div class="identity">
      <h1 class="identity__name">Tomasz Brelwik</h1>
      <p class="identity__title">Managing Director</p>
      <div class="rule"></div>
      <p class="contact"><b>P:</b> 020 5194 6281 | <b>M:</b> 07845139072</p>
      <p class="contact"><b>E:</b> tomasz@varkelt.co.uk | <span class="web">www.varkelt.co.uk</span></p>
    </div>
    <div class="services">
      <ul>
        <li>Kitchen Renovations</li>
        <li>Bathroom Renovations</li>
        <li>House Renovations</li>
        <li>Garage Conversions</li>
        <li>Extensions</li>
      </ul>
      <ul>
        <li>Loft Conversions</li>
        <li>Conservatories</li>
        <li>Carpentry</li>
        <li>Tiling</li>
        <li>Electrical</li>
      </ul>
      <ul>
        <li>Plumbing &amp; Heating</li>
        <li>Bricklaying</li>
        <li>Landscaping</li>
        <li>Decorating</li>
        <li>Plastering</li>
      </ul>
    </div>
    <div class="band band--bottom"></div>
  </section>

  <section class="card card--brand">
    <div class="tab tab--left"></div>
    <div class="tab tab--right"></div>
    <div class="brand">
      <span class="brand__name">Varkelt</span>
      <span class="brand__sub">Construction Ltd</span>
    </div>
  </section>
</body>
</html>
```